770 76 Chiro Brochure

https://files.vornaledge.net/sheet/q/84TxRm_wLz-Kq_PYbnHcVe391zd_4RQlmJTsPAk92x6/view?src=link

Brochure to show chiropractors about our program

```html
<!DOCTYPE html>
<html lang="en">
<head>
<meta charset="utf-8">
<title>Chiropractic Billboard Program Brochure</title>
<link href="https://fonts.googleapis.com/css2?family=Anton&family=Bowlby+One&family=Montserrat:wght@500;600;700;800;900&display=swap" rel="stylesheet">
<style>
  :root{
    --navy:#0b2f6b;
    --sky-top:#0a3a8c;
    --sky-mid:#2f7fd0;
    --sky-low:#8fc3ec;
    --grass:#3f9a1e;
    --grass-dark:#276b12;
    --brand-green:#2e9a3a;
    --icon-green:#3f8f2f;
    --yellow:#f7c81c;
    --red:#e3211f;
    --ad-bg:#0f1c12;
    --ad-glow:#1e3a1c;
    --white:#ffffff;
    --ink:#1c1c1c;
    --stage:#e4e5e7;
  }
  *{box-sizing:border-box;margin:0;padding:0}
  html,body{width:986px;height:1200px;overflow:hidden;background:var(--stage)}
  body{font-family:"Montserrat",sans-serif;position:relative}

  .spread{position:absolute;left:23px;width:940px;height:570px;display:flex;box-shadow:0 6px 18px rgba(0,0,0,.18)}
  .spread--outside{top:20px}
  .spread--inside{top:610px}
  .page{position:relative;width:470px;height:570px;overflow:hidden}

  /* outside spread */
  .scenery{position:absolute;inset:0;background:linear-gradient(180deg,var(--sky-top) 0%,var(--sky-mid) 45%,var(--sky-low) 72%,var(--grass) 80%,var(--grass-dark) 100%)}

  .cover-title{position:absolute;top:30px;left:0;width:100%;text-align:center;font-family:"Bowlby One",sans-serif;color:var(--white);line-height:.95}
  .cover-title__main{display:block;font-size:44px;letter-spacing:.5px}
  .cover-title__sub{display:block;font-size:31px;margin-top:2px}
  .cover-pill{position:absolute;top:132px;left:40px;width:390px;height:42px;background:var(--yellow);border-radius:10px;display:flex;align-items:center;justify-content:center;gap:10px;font-family:"Montserrat",sans-serif;font-weight:900;font-size:25px;color:var(--navy)}
  .cover-pill::before,.cover-pill::after{content:"";width:26px;height:3px;background:var(--navy)}
  .cover-partner{position:absolute;top:186px;left:0;width:100%;text-align:center;color:var(--white);font-size:11px;line-height:1.35;font-weight:500}
  .cover-partner strong{font-weight:800}

  /* billboard ad */
  .ad{position:absolute;width:410px;height:112px;background:radial-gradient(circle at 70% 50%,var(--ad-glow) 0%,var(--ad-bg) 70%);overflow:hidden;padding:7px 10px;color:var(--white);border:2px solid #0a120b}
  .ad__photo{position:absolute;right:0;top:0;width:118px;height:100%;background:linear-gradient(160deg,#b98b6a 0%,#6f4f3b 55%,#e9ecef 100%)}
  .ad__hook{font-family:"Anton",sans-serif;font-size:15px;color:var(--yellow);line-height:1;white-space:nowrap}
  .ad__injured{font-size:27px;color:var(--red);margin-right:4px}
  .ad__call{display:flex;align-items:center;gap:6px;margin-top:1px}
  .ad__callnow{font-weight:900;font-size:11px;line-height:.95;color:var(--yellow)}
  .ad__number{font-family:"Anton",sans-serif;font-size:34px;line-height:1;white-space:nowrap}
  .ad__sub{font-size:7.5px;font-weight:600;letter-spacing:.3px;margin-top:2px;white-space:nowrap}
  .ad__foot{display:flex;align-items:center;justify-content:space-between;width:280px;margin-top:5px}
  .ad__brand{display:flex;align-items:center;gap:4px;font-size:10px;font-weight:700;white-space:nowrap}
  .ad__brand::before{content:"";width:9px;height:9px;border-radius:50%;background:var(--white)}
  .ad__tag{background:var(--yellow);color:var(--ink);font-weight:900;font-size:11px;padding:2px 10px;border-radius:3px;white-space:nowrap}
  .ad__doctors{position:absolute;left:130px;bottom:4px;font-size:6px;font-weight:700;white-space:nowrap}

  .back-ads .ad{left:30px}
  .back-ads .ad:nth-child(2){top:35px}
  .back-ads .ad:nth-child(3){top:161px}
  .back-ads .ad:nth-child(4){top:287px}
  .back-ads .ad:nth-child(5){top:413px}
  .cover .ad{top:232px;left:30px}

  /* inside spread */
  .page--inside{background:var(--white)}
  .top-band{position:absolute;top:0;left:0;width:470px;height:40px}
  .field{position:absolute;left:0;bottom:0;width:100%;height:90px;background:linear-gradient(180deg,rgba(255,255,255,0) 0%,#9fd07a 35%,var(--grass) 65%,var(--grass-dark) 100%)}

  .bar{position:absolute;font-weight:800;font-size:11.5px;padding:7px 14px;border-radius:0 12px 0 12px;letter-spacing:.2px;white-space:nowrap}
  .bar--yellow{background:var(--yellow);color:var(--navy)}
  .bar--navy{background:var(--navy);color:var(--white)}

  .points{position:absolute;top:104px;left:28px;width:420px;list-style:none}
  .points li{display:flex;gap:10px;font-size:10.5px;line-height:1.35;color:var(--ink);margin-bottom:11px}
  .points svg{flex:none;width:16px;height:16px;margin-top:3px}
  .points strong{font-weight:800}

  .includes{position:absolute;top:290px;left:28px;list-style:none}
  .includes li{display:flex;align-items:center;gap:24px;height:70px;font-size:15px;font-weight:700;color:var(--ink)}
  .includes .icon{width:58px;height:58px;border-radius:50%;background:var(--icon-green);display:flex;align-items:center;justify-content:center;border:3px solid #d9ecd3}
  .includes svg{width:30px;height:30px}

  .intro{position:absolute;top:92px;left:28px;width:414px;font-size:10.5px;line-height:1.45;color:var(--ink);text-align:justify}
  .cities{position:absolute;top:232px;left:28px;width:414px;font-size:10.5px;line-height:1.5;color:var(--ink)}
  .inside-ad{position:absolute;top:360px;left:150px;transform:scale(.72);transform-origin:top left}
  .inside-ad .ad{position:relative}
</style>
</head>
<body>

<section class="spread spread--outside">
  <div class="page back">
    <div class="scenery" role="img" aria-label="Blue sky fading into a green grass field"></div>
    <div class="back-ads">
      <span></span>
      <article class="ad">
        <div class="ad__photo" role="img" aria-label="Photo of a chiropractor in a white coat"></div>
        <p class="ad__hook"><span class="ad__injured">INJURED</span>IN A CAR ACCIDENT?</p>
        <div class="ad__call"><span class="ad__callnow">CALL<br>NOW</span><span class="ad__number">(555) 01-SPINE</span></div>
        <p class="ad__sub">SAME DAY APPOINTMENTS | LOCATIONS ACROSS GEORGIA</p>
        <div class="ad__foot"><span class="ad__brand">Renew Motion</span><span class="ad__tag">NECK &amp; BACK PAIN</span></div>
      </article>
      <article class="ad">
        <div class="ad__photo" role="img" aria-label="Photo of two chiropractors in purple scrubs"></div>
        <p class="ad__hook"><span class="ad__injured">INJURED</span>IN A CAR ACCIDENT?</p>
        <div class="ad__call"><span class="ad__callnow">CALL<br>NOW</span><span class="ad__number">(555) 01-SPINE</span></div>
        <p class="ad__sub">SAME DAY APPOINTMENTS | LOCATIONS ACROSS GEORGIA</p>
        <div class="ad__foot"><span class="ad__brand">Midtown Spine &amp; Rehab</span><span class="ad__tag">NECK &amp; BACK PAIN</span></div>
      </article>
      <article class="ad">
        <div class="ad__photo" role="img" aria-label="Photo of a smiling chiropractor"></div>
        <p class="ad__hook"><span class="ad__injured">INJURED</span>IN A CAR ACCIDENT?</p>
        <div class="ad__call"><span class="ad__callnow">CALL<br>NOW</span><span class="ad__number">(555) 01-SPINE</span></div>
        <p class="ad__sub">SAME DAY APPOINTMENTS | LOCATIONS ACROSS GEORGIA</p>
        <div class="ad__foot"><span class="ad__brand">Renew Motion</span><span class="ad__tag">NECK &amp; BACK PAIN</span></div>
      </article>
      <article class="ad">
        <div class="ad__photo" role="img" aria-label="Photo of a chiropractor in a lab coat"></div>
        <p class="ad__hook"><span class="ad__injured">INJURED</span>IN A CAR ACCIDENT?</p>
        <div class="ad__call"><span class="ad__callnow">CALL<br>NOW</span><span class="ad__number">(555) 01-SPINE</span></div>
        <p class="ad__sub">SAME DAY APPOINTMENTS | LOCATIONS ACROSS GEORGIA</p>
        <div class="ad__foot"><span class="ad__brand">Clinica Vega</span><span class="ad__tag">HABLA ESPANOL</span></div>
      </article>
    </div>
  </div>

  <div class="page cover">
    <div class="scenery" role="img" aria-label="Blue sky over a grass field with a billboard pole and wind turbines"></div>
    <h1 class="cover-title"><span class="cover-title__main">CHIROPRACTIC</span><span class="cover-title__sub">BILLBOARD PROGRAM</span></h1>
    <p class="cover-pill">PERSONAL INJURY</p>
    <p class="cover-partner">WE PARTNER WITH<br><strong>GEORGIA CHIROPRACTORS.</strong></p>
    <article class="ad">
      <div class="ad__photo" role="img" aria-label="Photo of a smiling chiropractor"></div>
      <p class="ad__hook"><span class="ad__injured">INJURED</span>IN A CAR ACCIDENT?</p>
      <div class="ad__call"><span class="ad__callnow">CALL<br>NOW</span><span class="ad__number">(555) 01-SPINE</span></div>
      <p class="ad__sub">SAME DAY APPOINTMENTS | LOCATIONS ACROSS GEORGIA</p>
      <div class="ad__foot"><span class="ad__brand">Oakline Rehab</span><span class="ad__tag">HABLA ESPANOL</span></div>
    </article>
  </div>
</section>

<section class="spread spread--inside">
  <div class="page page--inside">
    <svg class="top-band" viewBox="0 0 470 40" preserveAspectRatio="none"><path d="M0 22 Q235 4 470 0 L470 0 L0 0 Z" fill="var(--brand-green)"/><path d="M0 22 Q235 4 470 0 L470 6 Q235 10 0 28 Z" fill="#ffffff"/></svg>
    <h2 class="bar bar--yellow" style="top:58px;left:20px">HOW TO DOMINATE PERSONAL INJURY ADVERTISING</h2>
    <ul class="points">
      <li><svg viewBox="0 0 16 16"><path d="M2 9 L6 13 L14 3" fill="none" stroke="var(--brand-green)" stroke-width="3" stroke-linecap="round" stroke-linejoin="round"/></svg><span><strong>(555) 01-SPINE</strong> is the preeminent vanity phone number for Chiropractors in Georgia to dominate personal injury advertising.</span></li>
      <li><svg viewBox="0 0 16 16"><path d="M2 9 L6 13 L14 3" fill="none" stroke="var(--brand-green)" stroke-width="3" stroke-linecap="round" stroke-linejoin="round"/></svg><span><strong>(555) 01-SPINE</strong> is more valuable than ever because of digital advertising.</span></li>
      <li><svg viewBox="0 0 16 16"><path d="M2 9 L6 13 L14 3" fill="none" stroke="var(--brand-green)" stroke-width="3" stroke-linecap="round" stroke-linejoin="round"/></svg><span>See how <strong>(555) 01-SPINE</strong> proved to substantially increase ROI through the Searchly Ads Algorithm and increase your Searchly Quality Score.</span></li>
    </ul>
    <h2 class="bar bar--navy" style="top:246px;left:20px;padding-left:30px;padding-right:60px">EVERY BILLBOARD WE CREATE INCLUDES</h2>
    <ul class="includes">
      <li><span class="icon"><svg viewBox="0 0 30 30"><circle cx="15" cy="9" r="6" fill="#fff"/><path d="M4 28 Q4 17 15 17 Q26 17 26 28 Z" fill="#fff"/><path d="M11 18 v4 a3 3 0 0 0 6 0" fill="none" stroke="var(--icon-green)" stroke-width="1.6"/></svg></span>Chiropractors Doctors Photo</li>
      <li><span class="icon"><svg viewBox="0 0 30 30"><path d="M7 3 V23 H27 M3 7 H23 V27" fill="none" stroke="#fff" stroke-width="2.5"/><path d="M11 19 L22 8" stroke="#fff" stroke-width="3" stroke-linecap="round"/></svg></span>Your Brand / Logo on the billboards</li>
      <li><span class="icon"><svg viewBox="0 0 30 30"><path d="M8 3 L12 3 L14 9 L11 11 Q13 17 19 19 L21 16 L27 18 L27 22 Q26 27 21 27 Q5 25 3 9 Q3 4 8 3 Z" fill="#fff"/></svg></span>Direct dial forwarded to your office</li>
    </ul>
    <div class="field" role="img" aria-label="Green grass field along the bottom edge"></div>
  </div>

  <div class="page page--inside">
    <svg class="top-band" viewBox="0 0 470 40" preserveAspectRatio="none"><path d="M0 0 Q235 0 470 0 L470 0 L0 0 Z M0 0 L470 0 L470 10 Q235 14 0 22 Z" fill="var(--brand-green)"/></svg>
    <h2 class="bar bar--navy" style="top:52px;left:20px;padding-right:150px">REACH NEW CLIENTS / PATIENTS IN A BIG WAY!</h2>
    <p class="intro">Expand your marketing mix and grow your business through our professionally designed billboards that showcase your photo, name, logo, at any time and in any place. Billboards set you apart from the competition by building credibility and brand recognition. Billboards serve as an important top-of-funnel channel and in conjunction with your current marketing channels, will increase your effectiveness.</p>
    <h2 class="bar bar--navy" style="top:192px;left:20px;font-size:10.5px">GEORGIA BILLBOARD LOCATIONS (OVER 200 BOARDS AVAILABLE)</h2>
    <p class="cities">Albany - Athens - Atlanta - Augusta - Blairville - Blackshear - Blue Ridge - Conyers - Valdosta Cummings - Dalton - Ft Oglethorpe - Hazelhurst - Jesup - Kennesaw - Macon - McDonough Savannah - Thomasville - Toccoa - Young Harris - Watkinsville - Bogart - Winder - Sandersville - Tifton - Cordele - Clayton - Milledgeville - Dublin - Chatsworth - Mineral Bluff - Eatonsville Hinesville - Warner Robins - Moultrie - LaFayette - Senoia - Ackworth - Camilla - Dawsonville Barnesville - Bainbridge - Cairo - Americus</p>
    <div class="inside-ad">
      <article class="ad">
        <div class="ad__photo" role="img" aria-label="Photo of two chiropractors in purple scrubs"></div>
        <p class="ad__hook"><span class="ad__injured">INJURED</span>IN A CAR ACCIDENT?</p>
        <div class="ad__call"><span class="ad__callnow">CALL<br>NOW</span><span class="ad__number">(555) 01-SPINE</span></div>
        <p class="ad__sub">SAME DAY APPOINTMENTS | LOCATIONS ACROSS GEORGIA</p>
        <div class="ad__foot"><span class="ad__brand">Midtown Spine &amp; Rehab</span><span class="ad__tag">NECK &amp; BACK PAIN</span></div>
        <p class="ad__doctors">DR. DANA REED, D.C &amp; DR. MARCUS HALE, D.C</p>
      </article>
    </div>
    <div class="field" role="img" aria-label="Green grass field with a billboard pole"></div>
  </div>
</section>

</body>
</html>
```